Open Harbor book needs a cover design

I need a front and back cover design that demonstrates a strong sense of possibility that trust can be repaired even if things look bleak. Repairing trust is difficult, but this book is full of wisdom, proven strategies, and doctoral research to help people strengthen relationships and improve trust. It can help any group: business, nonprofit, education, service. Showing diversity of groups and people is very important. For the cover title, there should be a play on words: "Open Harbor: Is it? Within Reach" should have the words "is it?" crossed out and the words "It IS! should be replaced there in a striking way. Perhaps in red ink. For publishing purposes, book will be titled Open Harbor: It IS Within Reach! Please see the attachment for an example. The book layout is approximately 260 pages.

A business self-help book, but the target is any person in a group that feels they have lost trust in each other. It can be just a normal person struggling in a volunteer group they are a part of, or a supervisor whose group is not working well together. It can be a leader who just wants their group to be stronger.

Business Management

• Allise - I believe is being used on the interior of the book for the title page and headings

• Show hope and possibility in the midst of difficulty. Must have a play on the words in the title "Open Harbor: Is it? Within Reach" with crossing out "is it?" with "It IS!" (see attached example) Must include the author's name: Marla Quentin, PhD Must include a smaller tagline: "Practical Steps to Move Teams Forward Again"
• Showing diverse people, or hands. Diverse kinds of groups - not just business. A colorful cover. Maybe show the complexity of trust when it is broken...broken pieces of trust that are then picked up and put together when people work together. Could show people (or images of hands) or other ways to show that it's a choice and it is possible to repair broken trust. I'd also like to convey a sense of a group - not just random people. That they have something at stake to work on repairing trust together and this book can help them.
• If images of people are used, just showing one gender or race is not okay. Nor just binary choices: like an image containing one man and one woman, or one white person and one person of color - otherwise it seems that the book on Open Harbor is about race or gender relations.

```html
<!DOCTYPE html>
<html lang="en">
<head>
<meta charset="utf-8">
<title>Open Harbor – Book Cover</title>
<link rel="stylesheet" href="https://fonts.googleapis.com/css2?family=Neucha&family=Pathway+Gothic+One&display=swap">
<style>
  :root {
    --page-bg: #ecebe8;
    --cover-white: #ffffff;
    --ink-navy: #14202e;
    --ink-dark: #1e1e1e;
    --teal: #27a9c4;
    --teal-band: #2ba6c2;
    --teal-spine: #2a9fba;
    --strike-red: #d0202a;
    --rule-grey: #6b6b6b;
    --photo-top-a: #c4c7ce;
    --photo-top-b: #e3e1de;
    --photo-wall: #f1f0ec;
    --photo-red: #b5303a;
    --photo-skin: #d6a98c;
    --photo-blue: #9fb4cf;
    --photo-orange: #e48a55;
    --photo-check: #6c7fa6;
    --photo-table: #ddd3c6;
  }
  * { box-sizing: border-box; margin: 0; padding: 0; }
  html, body { width: 1200px; height: 800px; overflow: hidden; }
  body {
    background: var(--page-bg);
    font-family: "Neucha", "Trebuchet MS", sans-serif;
    position: relative;
  }
  .book {
    position: absolute;
    left: 340px; top: 40px;
    width: 520px; height: 720px;
    display: flex;
    box-shadow: 0 6px 18px rgba(0,0,0,0.18);
  }
  .book-spine {
    position: relative;
    width: 40px; height: 720px;
    background: var(--teal-spine);
  }
  .spine-text {
    position: absolute; left: 50%; top: 0;
    transform-origin: 0 0;
    transform: rotate(90deg) translateY(-50%);
    white-space: nowrap;
    line-height: 1;
  }
  .spine-title {
    top: 70px;
    font-family: "Pathway Gothic One", "Arial Narrow", sans-serif;
    font-size: 36px; letter-spacing: 1px;
    color: var(--cover-white);
  }
  .spine-title .spine-first { color: var(--ink-navy); }
  .spine-author { top: 430px; font-size: 19px; color: var(--cover-white); }

  .book-cover {
    position: relative;
    width: 480px; height: 720px;
    background: var(--cover-white);
    overflow: hidden;
  }
  .group-photo-top {
    position: absolute; left: 70px; top: 0;
    width: 340px; height: 190px;
    background: linear-gradient(180deg, var(--photo-top-a) 0%, var(--photo-top-b) 65%, var(--cover-white) 100%);
    opacity: 0.8;
  }
  .title-block { position: absolute; left: 0; top: 72px; width: 100%; text-align: center; }
  .title {
    display: block;
    font-family: "Pathway Gothic One", "Arial Narrow", sans-serif;
    font-weight: 400; font-size: 84px; line-height: 66px;
  }
  .title-line-one { color: var(--ink-navy); }
  .title-line-two { color: var(--teal); }
  .answer { position: absolute; left: 0; width: 100%; text-align: center; top: 226px; font-size: 40px; line-height: 44px; color: var(--ink-dark); }
  .question {
    position: absolute; left: 0; width: 100%; text-align: center; top: 270px;
    font-size: 22px; line-height: 24px; color: var(--ink-dark);
  }
  .question span { position: relative; display: inline-block; }
  .question svg { position: absolute; left: -2px; top: 0; width: calc(100% + 4px); height: 100%; }
  .title-end {
    position: absolute; left: 0; width: 100%; text-align: center; top: 296px;
    font-family: "Pathway Gothic One", "Arial Narrow", sans-serif;
    font-size: 48px; line-height: 52px; color: var(--ink-dark);
  }
  .rule { position: absolute; left: 80px; width: 320px; height: 1px; background: var(--rule-grey); }
  .rule-upper { top: 362px; }
  .rule-lower { top: 422px; }
  .tagline {
    position: absolute; left: 0; width: 100%; top: 368px; text-align: center;
    font-family: "Pathway Gothic One", "Arial Narrow", sans-serif;
    font-size: 21px; line-height: 24px; text-transform: uppercase; color: var(--ink-dark);
  }
  .group-photo-bottom {
    position: absolute; left: 0; top: 424px; width: 480px; height: 248px;
    background:
      linear-gradient(180deg, var(--photo-wall) 0%, rgba(241,240,236,0) 30%, rgba(221,211,198,0) 70%, var(--photo-table) 100%),
      linear-gradient(90deg, var(--photo-red) 0%, var(--photo-skin) 22%, var(--photo-blue) 45%, var(--photo-orange) 68%, var(--photo-check) 100%);
  }
  .author-band {
    position: absolute; left: 0; top: 672px; width: 480px; height: 48px;
    background: var(--teal-band);
    color: var(--cover-white); font-size: 27px; text-align: center; line-height: 48px;
  }
</style>
</head>
<body>
  <div class="book">
    <aside class="book-spine">
      <p class="spine-text spine-title"><span class="spine-first">OPEN</span> HARBOR</p>
      <p class="spine-text spine-author">Marla Quentin, PhD</p>
    </aside>
    <main class="book-cover">
      <div class="group-photo-top" role="img" aria-label="Faded photo of a diverse group of people seated in a row, looking thoughtful"></div>
      <h1 class="title-block">
        <span class="title title-line-one">OPEN</span>
        <span class="title title-line-two">HARBOR</span>
      </h1>
      <p class="answer">It Is!</p>
      <p class="question"><span>Is It?<svg viewBox="0 0 60 24" preserveAspectRatio="none" aria-hidden="true"><line x1="0" y1="5" x2="60" y2="19" stroke="#d0202a" stroke-width="2"/><line x1="0" y1="19" x2="60" y2="5" stroke="#d0202a" stroke-width="2"/></svg></span></p>
      <p class="title-end">Within Reach</p>
      <div class="rule rule-upper"></div>
      <p class="tagline">Practical Steps to Move Teams<br>Forward Again</p>
      <div class="rule rule-lower"></div>
      <div class="group-photo-bottom" role="img" aria-label="Photo of a diverse team smiling and working together around a laptop at a table"></div>
      <p class="author-band">Marla Quentin, PhD</p>
    </main>
  </div>
</body>
</html>
```